New Business Card Design Project

We require a business card design for Vexalund, a newly established Indian company.
Our focus is on the development, manufacturing, and export of a diverse array of pharmaceutical products on a global scale. The card should convey a professional appearance, as our primary markets are in Africa, China, and Southeast Asian nations.
We envision a two-sided business card, with the reverse side dedicated to a logo set against a solid color or an elegantly designed pattern. The corners should be rounded. We would appreciate seeing both horizontal and vertical design options. We trust the designer to utilize their expertise in creating this design.

The content for the business card is included in the attached Word file.

Target Market(s)

Our primary markets are in Africa, China, and Southeast Asian, Latin America, Maldives, Sri Lanka

Industry/Entity Type

Pharmaceutical Manufacturing and Export

Contact Information for Business Card

Colors

Designer to choose colors to be used in the design.

Requirements
Must have
• The reverse side of the business card features solely the logo along with the tagline, "Care Across Borders."
Should not have
• The logo should not exceed two instances, encompassing both the front and back sides of the card.

```html
<!DOCTYPE html>
<html lang="en">
<head>
<meta charset="utf-8">
<title>Vexalund Business Card</title>
<link href="https://fonts.googleapis.com/css2?family=Montserrat:wght@400;700&family=Open+Sans:wght@400;600&display=swap" rel="stylesheet">
<style>
  :root{
    --stage:#222224;
    --paper:#ffffff;
    --ink:#1f1f22;
    --brand-blue:#2ea8e0;
    --brand-coral:#f0624d;
    --text-dark:#1a1a1a;
  }
  *{margin:0;padding:0;box-sizing:border-box}
  html,body{width:1200px;height:711px;overflow:hidden;background:var(--stage)}
  .stage{position:relative;width:1200px;height:711px;display:flex;align-items:center;justify-content:center;gap:40px}
  .card{position:relative;width:540px;height:309px;background:var(--paper);border-radius:22px;overflow:hidden;box-shadow:0 14px 30px rgba(0,0,0,.55)}

  /* back side */
  .card--back{display:flex;flex-direction:column;align-items:center;justify-content:center}
  .brand-mark{display:flex;align-items:center;gap:12px}
  .brand-dot{width:18px;height:18px;border-radius:50%;background:var(--brand-coral)}
  .brand-name{font-family:"Montserrat",sans-serif;font-weight:700;color:var(--brand-blue);font-size:58px;letter-spacing:1px;line-height:1}
  .tagline{margin-top:18px;font-family:"Montserrat",sans-serif;font-weight:400;color:var(--brand-blue);font-size:15px;letter-spacing:1px}

  /* front side */
  .front-panel{position:absolute;left:0;top:0;width:330px;height:309px}
  .front-info{position:absolute;right:0;top:0;width:260px;height:100%;padding:26px 26px 0 0;text-align:right}
  .front-info .brand-name{font-size:32px}
  .accent-bar{position:absolute;right:0;top:92px;width:22px;height:30px;background:var(--brand-coral)}
  .holder-name{margin-top:22px;font-family:"Open Sans",sans-serif;color:var(--brand-blue);font-size:22px;line-height:1.1}
  .holder-name b{font-family:"Montserrat",sans-serif;font-weight:700}
  .holder-role{font-family:"Open Sans",sans-serif;font-size:12px;color:var(--text-dark);margin-top:2px}
  .address{margin-top:16px;font-family:"Open Sans",sans-serif;font-size:11.5px;color:var(--brand-blue);line-height:1.45}
  .contacts{margin-top:12px;list-style:none;font-family:"Open Sans",sans-serif;font-size:12px;color:var(--text-dark);line-height:1.7}
  .contacts li{display:flex;justify-content:flex-end;align-items:center;gap:7px}
  .contacts svg{width:12px;height:12px;flex:none}
</style>
</head>
<body>
<main class="stage">

  <section class="card card--back" aria-label="Card reverse">
    <div class="brand-mark">
      <span class="brand-dot"></span>
      <span class="brand-name">Vexalund</span>
    </div>
    <p class="tagline">Care Across Borders.</p>
  </section>

  <section class="card card--front" aria-label="Card front">
    <svg class="front-panel" viewBox="0 0 330 309" aria-hidden="true">
      <path d="M0 0 H250 C300 40 320 120 318 180 C316 240 300 290 280 309 H0 Z" fill="var(--ink)"/>
    </svg>
    <span class="accent-bar"></span>
    <div class="front-info">
      <div class="brand-name">Vexalund</div>
      <p class="holder-name"><b>Arjun</b> K. Bhosale</p>
      <p class="holder-role">CEO</p>
      <p class="address">14, Nilgiri Nagar,<br>Akola, 444001, India</p>
      <ul class="contacts">
        <li>+91 98765 43210
          <svg viewBox="0 0 12 12"><rect x="3" y="0.8" width="6" height="10.4" rx="1.2" fill="none" stroke="var(--brand-coral)" stroke-width="1.3"/></svg>
        </li>
        <li>www.vexalund.com
          <svg viewBox="0 0 12 12"><circle cx="6" cy="6" r="5" fill="none" stroke="var(--brand-blue)" stroke-width="1.3"/><path d="M1 6H11M6 1C3.5 4 3.5 8 6 11M6 1C8.5 4 8.5 8 6 11" fill="none" stroke="var(--brand-blue)" stroke-width="1"/></svg>
        </li>
        <li>akbhosale@vexalund.com
          <svg viewBox="0 0 12 12"><rect x="0.8" y="2.5" width="10.4" height="7.5" fill="none" stroke="var(--brand-coral)" stroke-width="1.3"/><path d="M0.8 2.5L6 7L11.2 2.5" fill="none" stroke="var(--brand-coral)" stroke-width="1.2"/></svg>
        </li>
      </ul>
    </div>
  </section>

</main>
</body>
</html>
```